Harborline Auto LLC

Car Dealer Customer Service
Address: 2874 Cresthaven Road, Shelbyville, TN 37162
web: www.harborlineautoxq.net
email: harborlineautoxq@mailnest.example
Phone: (931) 555-0148
Phone: (629) 555-0173

```html
<!DOCTYPE html>
<html lang="en">
<head>
<meta charset="utf-8">
<title>Harborline Auto LLC – Business Card</title>
<link rel="stylesheet" href="https://fonts.googleapis.com/css2?family=Montserrat:wght@400;500;800&display=swap">
<style>
  :root {
    --brand-blue: #1f7fc0;
    --band-blue: #2a8cc9;
    --brand-gold: #ecb53f;
    --ink: #1c1c1c;
    --card: #ffffff;
    --backdrop: #e6e7e9;
  }
  * { box-sizing: border-box; margin: 0; padding: 0; }
  html, body { width: 1200px; height: 900px; overflow: hidden; }
  body {
    background: var(--backdrop);
    font-family: "Montserrat", sans-serif;
    color: var(--ink);
    position: relative;
  }
  .card {
    position: absolute;
    left: 250px;
    width: 700px;
    height: 400px;
    background: var(--card);
    box-shadow: 0 6px 18px rgba(0,0,0,0.12);
    overflow: hidden;
  }
  .card--front { top: 35px; }
  .card--back { top: 465px; }

  .wordmark {
    display: flex;
    align-items: center;
    gap: 14px;
    font-weight: 800;
    color: var(--brand-blue);
    text-transform: uppercase;
    letter-spacing: 0.5px;
    white-space: nowrap;
  }
  .wordmark__dot {
    border-radius: 50%;
    background: var(--brand-gold);
    flex: none;
  }
  .card--front .wordmark {
    position: absolute;
    left: 50%; top: 50%;
    transform: translate(-50%, -50%);
    font-size: 40px;
  }
  .card--front .wordmark__dot { width: 44px; height: 44px; }

  .card--back .wordmark {
    position: absolute;
    left: 40px; top: 118px;
    font-size: 24px;
    z-index: 1;
  }
  .card--back .wordmark__dot { width: 28px; height: 28px; }

  .divider {
    position: absolute;
    left: 354px; top: 66px;
    width: 1.5px; height: 160px;
    background: var(--brand-blue);
    z-index: 1;
  }
  .contact {
    position: absolute;
    left: 372px; top: 58px;
    font-size: 14px;
    line-height: 1.45;
    z-index: 1;
  }
  .contact__role { font-weight: 500; margin-bottom: 10px; }
  .contact__address { margin-bottom: 10px; margin-left: 10px; }
  .contact__list { list-style: none; margin-left: 12px; }
  .contact__item { display: flex; align-items: center; gap: 8px; font-size: 13.5px; }
  .contact__icon { width: 13px; height: 13px; flex: none; fill: var(--brand-blue); }
  .contact__web-domain { color: var(--brand-blue); }

  .wave { position: absolute; left: 0; bottom: 0; width: 700px; height: 400px; }
</style>
</head>
<body>
  <section class="card card--front" aria-label="Card front">
    <div class="wordmark"><span class="wordmark__dot"></span>Harborline Auto</div>
  </section>

  <section class="card card--back" aria-label="Card back">
    <svg class="wave" viewBox="0 0 700 400" aria-hidden="true">
      <path d="M0 388 C 200 376, 380 330, 500 298 S 640 258, 700 250 L700 400 L0 400 Z" fill="var(--band-blue)"/>
      <path d="M0 372 C 200 360, 380 314, 500 282 S 640 242, 700 234" fill="none" stroke="var(--brand-gold)" stroke-width="4"/>
    </svg>

    <div class="wordmark"><span class="wordmark__dot"></span>Harborline Auto</div>
    <div class="divider"></div>

    <div class="contact">
      <p class="contact__role">Car Dealer Customer Service</p>
      <p class="contact__address">2874 Cresthaven Road,<br>Shelbyville, TN 37162</p>
      <ul class="contact__list">
        <li class="contact__item">
          <svg class="contact__icon" viewBox="0 0 24 24"><path d="M6.6 10.8a15.1 15.1 0 0 0 6.6 6.6l2.2-2.2c.3-.3.7-.4 1-.2 1.1.4 2.3.6 3.6.6.6 0 1 .4 1 1V20c0 .6-.4 1-1 1A17 17 0 0 1 3 4c0-.6.4-1 1-1h3.5c.6 0 1 .4 1 1 0 1.3.2 2.5.6 3.6.1.3 0 .7-.2 1z"/></svg>
          (931) 555-0148
        </li>
        <li class="contact__item">
          <svg class="contact__icon" viewBox="0 0 24 24"><path d="M6.6 10.8a15.1 15.1 0 0 0 6.6 6.6l2.2-2.2c.3-.3.7-.4 1-.2 1.1.4 2.3.6 3.6.6.6 0 1 .4 1 1V20c0 .6-.4 1-1 1A17 17 0 0 1 3 4c0-.6.4-1 1-1h3.5c.6 0 1 .4 1 1 0 1.3.2 2.5.6 3.6.1.3 0 .7-.2 1z"/></svg>
          (629) 555-0173
        </li>
        <li class="contact__item">
          <svg class="contact__icon" viewBox="0 0 24 24"><path d="M2 5h20v14H2z M3 6l9 7 9-7" fill="var(--brand-blue)" stroke="#fff" stroke-width="1.5"/></svg>
          harborlineautoxq@mailnest.example
        </li>
        <li class="contact__item">
          <svg class="contact__icon" viewBox="0 0 24 24"><circle cx="12" cy="12" r="10"/><path d="M2 12h20M12 2c3 3 3 17 0 20M12 2c-3 3-3 17 0 20" fill="none" stroke="#fff" stroke-width="1.5"/></svg>
          <span>www.<span class="contact__web-domain">harborlineautoxq</span>.net</span>
        </li>
      </ul>
    </div>
  </section>
</body>
</html>
```